Vantoq Business Card Project showing the logo and a marbo image on the rear

Design a whacky but professional business card, the logo is for the front and the Marbo image is for the rear. Happy to consider other open source Marbo Images if the designer wants to select one from the web. Vantoq is a competitor to OMB.com.au and Pellory.com.au and is based around every property in Australia

Target Market(s)

Business

Contact Information for Business Card

Name, Title, Email, Web, Phone Number

Font styles to use
Other font styles liked:
• avenir

Requirements
Must have
• Image on Back logo on front
Nice to have
• Happy to consider other images on rear, preftably Colin Marbo. Image supplied I own, we can use open source other Marbo Images

```html
<!DOCTYPE html>
<html lang="en">
<head>
<meta charset="utf-8">
<title>Vantoq Business Card</title>
<link rel="stylesheet" href="https://fonts.googleapis.com/css2?family=Jost:wght@500;600&family=Roboto:wght@400&display=swap">
<style>
  :root {
    --backdrop: #ddd8d0;
    --card: #f2f3f3;
    --ink: #1d1d1d;
    --orange: #ef8a10;
    --orange-soft: #f29a28;
    --white: #ffffff;
  }
  * { box-sizing: border-box; margin: 0; padding: 0; }
  html, body {
    width: 1200px;
    height: 1054px;
    overflow: hidden;
    background: var(--backdrop);
  }
  .business-card {
    position: absolute;
    left: 100px;
    top: 227px;
    width: 1000px;
    height: 600px;
    background: var(--card);
    border-radius: 22px;
    box-shadow: 0 18px 40px rgba(0,0,0,0.12);
    font-family: "Roboto", Arial, sans-serif;
    color: var(--ink);
  }
  .brand {
    position: absolute;
    left: 51px;
    top: 52px;
    display: flex;
    align-items: center;
    gap: 34px;
  }
  .brand-square {
    width: 96px;
    height: 96px;
    background: var(--orange);
  }
  .brand-name {
    font-family: "Jost", "Helvetica Neue", sans-serif;
    font-weight: 600;
    font-size: 88px;
    line-height: 1;
    color: var(--ink);
  }
  .person-name {
    position: absolute;
    left: 51px;
    top: 244px;
    font-family: "Jost", "Helvetica Neue", sans-serif;
    font-weight: 600;
    font-size: 38px;
    line-height: 1.1;
    color: var(--orange);
  }
  .person-title {
    position: absolute;
    left: 51px;
    top: 295px;
    font-size: 25px;
    line-height: 1.2;
  }
  .contact-list {
    position: absolute;
    left: 51px;
    top: 370px;
    list-style: none;
  }
  .contact-item {
    display: flex;
    align-items: center;
    height: 38px;
    font-size: 25px;
  }
  .contact-icon {
    width: 24px;
    height: 24px;
    margin-right: 27px;
    flex: none;
  }
  .accent { color: var(--orange); }
  .address {
    position: absolute;
    left: 51px;
    top: 492px;
    font-size: 25px;
    line-height: 33px;
  }
  .brand-feature {
    position: absolute;
    left: 530px;
    top: 100px;
    width: 410px;
    height: 410px;
    border-radius: 50%;
    background: var(--orange-soft);
    display: flex;
    align-items: center;
    justify-content: center;
  }
  .brand-feature-name {
    font-family: "Jost", "Helvetica Neue", sans-serif;
    font-weight: 600;
    font-size: 84px;
    line-height: 1;
    color: var(--white);
  }
</style>
</head>
<body>
  <main class="business-card">
    <div class="brand">
      <div class="brand-square"></div>
      <div class="brand-name">Vantoq</div>
    </div>

    <h1 class="person-name">Owen Talbrook</h1>
    <p class="person-title">Founder &amp; CEO</p>

    <ul class="contact-list">
      <li class="contact-item">
        <svg class="contact-icon" viewBox="0 0 24 24" aria-hidden="true">
          <circle cx="12" cy="12" r="10" fill="none" stroke="#ef8a10" stroke-width="2"/>
          <path d="M8.5 7.5l2 2-1 1.3c.7 1.5 1.7 2.5 3.2 3.2l1.3-1 2 2-1.2 1.5c-3.8-.6-6.7-3.5-7.3-7.3z" fill="#ef8a10"/>
        </svg>
        (00) 4817 2095
      </li>
      <li class="contact-item">
        <svg class="contact-icon" viewBox="0 0 24 24" aria-hidden="true">
          <rect x="3" y="6" width="18" height="12" fill="#ef8a10"/>
          <path d="M3 6l9 7 9-7" fill="none" stroke="#f2f3f3" stroke-width="1.6"/>
        </svg>
        talbrook@vantoq.com
      </li>
      <li class="contact-item">
        <svg class="contact-icon" viewBox="0 0 24 24" aria-hidden="true">
          <circle cx="12" cy="12" r="9" fill="#ef8a10"/>
          <g fill="none" stroke="#f2f3f3" stroke-width="1.3">
            <ellipse cx="12" cy="12" rx="4" ry="9"/>
            <path d="M3 12h18M4.5 7.5h15M4.5 16.5h15"/>
          </g>
        </svg>
        <span>www.<span class="accent">vantoq</span>.com</span>
      </li>
    </ul>

    <p class="address">Level 4, 18 Corran Lane,<br>Sydney 2000, Australia</p>

    <div class="brand-feature">
      <span class="brand-feature-name">Vantoq</span>
    </div>
  </main>
</body>
</html>
```